Accountability Project Graphics

I want to create 10 social media graphics (new Instagram size 4:5 (1080 x 1350 pixels) focusing on our Quilvo Accountability App, using any of the 3 pictures attached. Use the attached pics only, NO RANDOM STOCK PHOTOGRAPHY. For the color scheme, use the landing page colors/fonts (attached).
You can add any of the 3 photos attached but I mainly need BOLD text that includes these headlines and sub-headlines on them.
Please NOTE for all the headlines below, also add this sub-headline on each graphic:
Stay Consistent with RT in Your Pocket!
Here are the headlines:
• Stop Starting Over Every Monday
• You don't need more willpower. You need more support
• Built for women who are tired of doing this alone
• When Motivation Fades, RT Checks In
• The Support System You've Been Missing
• Support When Motivation Disappears
• What if RT Checked in Every Day?
• The Missing Piece Isn't Another Diet
• Eat the food you love. Stay accountable every day.
• One Bad Meal Doesn't Mean You Failed
women over 40 trying to lose weight

```html
<!DOCTYPE html>
<html lang="en">
<head>
<meta charset="utf-8">
<title>Quilvo Accountability Graphics</title>
<link rel="stylesheet" href="https://fonts.googleapis.com/css2?family=Source+Serif+4:opsz,wght@8..60,700;8..60,800&family=Inter:wght@600;700&display=swap">
<style>
:root{
  --ink:#2a1838;
  --rose:#de4479;
  --blush:#fbe4ec;
  --blush-deep:#f6c3d3;
  --icon:#ef6f98;
  --frame:#000;
  --photo-dark:#1f2438;
  --photo-pink:#e86a98;
}
*{margin:0;padding:0;box-sizing:border-box}
html,body{width:1200px;height:1198px;overflow:hidden;background:var(--frame)}
.board{
  width:1200px;height:1198px;display:grid;
  grid-template-columns:repeat(5,1fr);grid-template-rows:repeat(4,1fr);
  gap:2px;background:var(--frame);
}
.post{
  position:relative;overflow:hidden;isolation:isolate;
  background:linear-gradient(160deg,#fdeef2 0%,var(--blush) 55%,#f9d6e1 100%);
}
.post::before{
  content:"";position:absolute;right:-70px;top:10px;width:240px;height:300px;
  border-radius:50%;background:var(--blush-deep);opacity:.55;z-index:0;
}
.post::after{
  content:"";position:absolute;left:-40px;bottom:-70px;width:220px;height:150px;
  border-radius:50%;background:#f8ccd9;opacity:.5;z-index:0;
}
.copy{position:absolute;left:14px;top:20px;z-index:5;width:124px}
.headline{
  font-family:"Source Serif 4",Georgia,serif;font-weight:800;
  font-size:var(--fs,24px);line-height:.98;letter-spacing:-.4px;color:var(--ink);
}
.headline .accent{color:var(--rose);font-style:normal}
.divider{position:relative;height:1px;background:var(--rose);opacity:.8;margin:9px 0 7px;width:92px}
.divider svg{position:absolute;left:50%;top:-4px;width:8px;height:8px;margin-left:-4px;fill:var(--rose)}
.tagline{font-family:"Inter",Arial,sans-serif;font-weight:700;font-size:8.5px;line-height:1.3;color:var(--ink)}
.tagline span{display:block;color:var(--rose);font-weight:600}
.icon{position:absolute;left:14px;bottom:18px;width:74px;height:74px;z-index:2;fill:var(--icon)}
.icon.faint{opacity:.35;width:96px;height:96px;bottom:6px;left:10px}
.photo{
  position:absolute;right:0;bottom:0;z-index:1;width:96px;height:80%;
  border-radius:48px 0 0 0;
  background:linear-gradient(180deg,#3a2c3a 0%,var(--photo-dark) 40%,#2b3150 100%);
}
.photo.hug{height:70%;background:linear-gradient(135deg,#2a1e26 0%,var(--photo-pink) 55%,#eef3d6 100%)}
.photo.duo{height:76%;background:linear-gradient(90deg,#2c3656 0%,#eef0f4 45%,#2a3a5a 100%)}
</style>
</head>
<body>
<svg width="0" height="0" style="position:absolute" aria-hidden="true">
  <defs>
    <symbol id="i-heart" viewBox="0 0 24 24"><path d="M12 21s-8-5.3-10-10.2C.6 7.3 2.8 4 6.3 4c2.2 0 3.7 1.3 4.7 2.7h2C14 5.3 15.5 4 17.7 4 21.2 4 23.4 7.3 22 10.8 20 15.7 12 21 12 21z"/></symbol>
    <symbol id="i-puzzle" viewBox="0 0 24 24"><path d="M4 8h4a2.5 2.5 0 1 1 5 0h4v4a2.5 2.5 0 1 1 0 5v4H4v-4a2.5 2.5 0 1 0 0-5z"/></symbol>
    <symbol id="i-phone" viewBox="0 0 24 24"><path d="M12 2a10 9 0 0 0-8.6 13.6L2 21l5.6-1.7A10 9 0 1 0 12 2z"/><path fill="#fbe4ec" d="M8.6 7.2l1.6-.3 1 2.3-1 .9a6 6 0 0 0 2.8 2.8l.9-1 2.3 1-.3 1.6c-.2.6-.9 1-1.6.9A8 8 0 0 1 7.7 8.8c-.1-.7.3-1.4.9-1.6z"/></symbol>
    <symbol id="i-calendar" viewBox="0 0 24 24"><path d="M3 5h18v16H3z" fill="none" stroke="currentColor" stroke-width="2"/><path d="M3 5h18v4H3zM7 2h2v5H7zM15 2h2v5h-2zM6 12h3v2H6zM11 12h3v2h-3zM6 16h3v2H6zM11 16h3v2h-3z"/></symbol>
    <symbol id="i-bell" viewBox="0 0 24 24"><path d="M12 2a2 2 0 0 1 2 2 6 6 0 0 1 4 6v4l2 3H4l2-3v-4a6 6 0 0 1 4-6 2 2 0 0 1 2-2zM9.5 19h5a2.5 2.5 0 0 1-5 0z"/></symbol>
    <symbol id="i-chat" viewBox="0 0 24 24"><path d="M3 7h11v9H8l-4 3v-3H3z" fill="none" stroke="currentColor" stroke-width="1.8"/><circle cx="6.5" cy="11.5" r="1"/><circle cx="9" cy="11.5" r="1"/><circle cx="11.5" cy="11.5" r="1"/><circle cx="17.5" cy="6.5" r="4.5"/><path d="M15.5 6.5l1.5 1.5 2.5-3" fill="none" stroke="#fbe4ec" stroke-width="1.4"/></symbol>
  </defs>
</svg>

<main class="board">

  <article class="post">
    <div class="copy"><h2 class="headline" style="--fs:25px">The Support System <em class="accent">You’ve Been Missing</em></h2><div class="divider"><svg><use href="#i-heart"/></svg></div><p class="tagline">Stay Consistent with<span>RT in Your Pocket!</span></p></div>
    <svg class="icon"><use href="#i-heart"/></svg>
    <div class="photo hug" role="img" aria-label="Photo of two women sharing a joyful hug"></div>
  </article>

  <article class="post">
    <div class="copy"><h2 class="headline" style="--fs:21px">Support When <em class="accent">Motivation Disappears</em></h2><div class="divider"><svg><use href="#i-heart"/></svg></div><p class="tagline">Stay Consistent with<span>RT in Your Pocket!</span></p></div>
    <svg class="icon"><use href="#i-heart"/></svg>
    <div class="photo duo" role="img" aria-label="Photo of two women standing together laughing"></div>
  </article>

  <article class="post">
    <div class="copy"><h2 class="headline" style="--fs:19px">Eat the food you love. <em class="accent">Stay accountable every day.</em></h2><div class="divider"><svg><use href="#i-heart"/></svg></div><p class="tagline">Stay Consistent with<span>RT in Your Pocket!</span></p></div>
    <svg class="icon"><use href="#i-heart"/></svg>
    <div class="photo" role="img" aria-label="Photo of the coach smiling, hand on hip"></div>
  </article>

  <article class="post">
    <div class="copy"><h2 class="headline" style="--fs:24px">The Missing Piece <em class="accent">Isn’t Another Diet</em></h2><div class="divider"><svg><use href="#i-heart"/></svg></div><p class="tagline">Stay Consistent with<span>RT in Your Pocket!</span></p></div>
    <svg class="icon"><use href="#i-puzzle"/></svg>
    <div class="photo" role="img" aria-label="Photo of the coach smiling, hand on hip"></div>
  </article>

  <article class="post">
    <div class="copy"><h2 class="headline" style="--fs:21px">When <em class="accent">Motivation</em> Fades, <em class="accent">RT Checks In</em></h2><div class="divider"><svg><use href="#i-heart"/></svg></div><p class="tagline">Stay Consistent with<span>RT in Your Pocket!</span></p></div>
    <svg class="icon"><use href="#i-phone"/></svg>
    <div class="photo" role="img" aria-label="Photo of the coach smiling, hand on hip"></div>
  </article>

  <article class="post">
    <div class="copy"><h2 class="headline" style="--fs:24px">One Bad Meal <em class="accent">Doesn’t Mean You Failed</em></h2><div class="divider"><svg><use href="#i-heart"/></svg></div><p class="tagline">Stay Consistent with<span>RT in Your Pocket!</span></p></div>
    <svg class="icon"><use href="#i-heart"/></svg>
    <div class="photo hug" role="img" aria-label="Photo of two women sharing a joyful hug"></div>
  </article>

  <article class="post">
    <div class="copy"><h2 class="headline" style="--fs:24px">Stop <em class="accent">Starting Over</em> Every Monday</h2><div class="divider"><svg><use href="#i-heart"/></svg></div><p class="tagline">Stay Consistent with<span>RT in Your Pocket!</span></p></div>
    <svg class="icon" style="color:var(--icon)"><use href="#i-calendar"/></svg>
    <div class="photo" role="img" aria-label="Photo of the coach smiling, hand on hip"></div>
  </article>

  <article class="post">
    <div class="copy"><h2 class="headline" style="--fs:20px">What if RT Checked in <em class="accent" style="font-size:27px">Every Day?</em></h2><div class="divider"><svg><use href="#i-heart"/></svg></div><p class="tagline">Stay Consistent with<span>RT in Your Pocket!</span></p></div>
    <svg class="icon"><use href="#i-bell"/></svg>
    <div class="photo" role="img" aria-label="Photo of the coach smiling, hand on hip"></div>
  </article>

  <article class="post">
    <div class="copy"><h2 class="headline" style="--fs:20px">You don’t need more willpower. <em class="accent">You need more support</em></h2><div class="divider"><svg><use href="#i-heart"/></svg></div><p class="tagline">Stay Consistent with<span>RT in Your Pocket!</span></p></div>
    <svg class="icon"><use href="#i-heart"/></svg>
    <div class="photo hug" role="img" aria-label="Photo of two women sharing a joyful hug"></div>
  </article>

  <article class="post">
    <div class="copy"><h2 class="headline" style="--fs:21px">Support When <em class="accent">Motivation</em> Disappears</h2><div class="divider"><svg><use href="#i-heart"/></svg></div><p class="tagline">Stay Consistent with<span>RT in Your Pocket!</span></p></div>
    <svg class="icon"><use href="#i-heart"/></svg>
    <div class="photo hug" style="height:60%" role="img" aria-label="Photo of two women sharing a joyful hug"></div>
  </article>

  <article class="post">
    <div class="copy"><h2 class="headline" style="--fs:24px">Stop Starting Over <em class="accent">Every Monday</em></h2><div class="divider"><svg><use href="#i-heart"/></svg></div><p class="tagline">Stay Consistent with<span>RT in Your Pocket!</span></p></div>
    <svg class="icon faint" style="color:var(--icon)"><use href="#i-calendar"/></svg>
    <div class="photo" role="img" aria-label="Photo of the coach smiling, hand on hip"></div>
  </article>

  <article class="post">
    <div class="copy"><h2 class="headline" style="--fs:24px">The Missing Piece <em class="accent">Isn’t Another Diet</em></h2><div class="divider"><svg><use href="#i-heart"/></svg></div><p class="tagline">Stay Consistent with<span>RT in Your Pocket!</span></p></div>
    <svg class="icon"><use href="#i-puzzle"/></svg>
    <div class="photo" role="img" aria-label="Photo of the coach smiling, hand on hip"></div>
  </article>

  <article class="post">
    <div class="copy"><h2 class="headline" style="--fs:24px">The <em class="accent">Support System</em> You’ve Been <em class="accent">Missing</em></h2><div class="divider"><svg><use href="#i-heart"/></svg></div><p class="tagline">Stay Consistent with<span>RT in Your Pocket!</span></p></div>
    <svg class="icon"><use href="#i-heart"/></svg>
    <div class="photo hug" style="height:58%" role="img" aria-label="Photo of two women sharing a joyful hug"></div>
  </article>

  <article class="post">
    <div class="copy"><h2 class="headline" style="--fs:23px">What if <em class="accent">RT</em> Checked in <em class="accent">Every Day?</em></h2><div class="divider"><svg><use href="#i-heart"/></svg></div><p class="tagline">Stay Consistent with<span>RT in Your Pocket!</span></p></div>
    <svg class="icon"><use href="#i-bell"/></svg>
    <div class="photo" role="img" aria-label="Photo of the coach smiling, hand on hip"></div>
  </article>

  <article class="post">
    <div class="copy"><h2 class="headline" style="--fs:23px">Built for <em class="accent">women</em> who are tired of doing this <em class="accent">alone</em></h2><div class="divider"><svg><use href="#i-heart"/></svg></div><p class="tagline">Stay Consistent with<span>RT in Your Pocket!</span></p></div>
    <svg class="icon"><use href="#i-heart"/></svg>
    <div class="photo duo" style="height:68%" role="img" aria-label="Photo of two women standing together laughing"></div>
  </article>

  <article class="post">
    <div class="copy"><h2 class="headline" style="--fs:20px">You don’t need more willpower. <em class="accent">You need more support</em></h2><div class="divider"><svg><use href="#i-heart"/></svg></div><p class="tagline">Stay Consistent with<span>RT in Your Pocket!</span></p></div>
    <svg class="icon"><use href="#i-heart"/></svg>
    <div class="photo hug" role="img" aria-label="Photo of two women sharing a joyful hug"></div>
  </article>

  <article class="post">
    <div class="copy"><h2 class="headline" style="--fs:19px">Eat the food you love. <em class="accent">Stay accountable every day.</em></h2><div class="divider"><svg><use href="#i-heart"/></svg></div><p class="tagline">Stay Consistent with<span>RT in Your Pocket!</span></p></div>
    <svg class="icon"><use href="#i-heart"/></svg>
    <div class="photo" role="img" aria-label="Photo of the coach smiling, hand on hip"></div>
  </article>

  <article class="post">
    <div class="copy" style="top:40px"><h2 class="headline" style="--fs:21px">When <em class="accent">Motivation</em> Fades, <em class="accent">RT Checks In</em></h2><div class="divider"><svg><use href="#i-heart"/></svg></div><p class="tagline">Stay Consistent with<span>RT in Your Pocket!</span></p></div>
    <svg class="icon" style="color:var(--icon)"><use href="#i-chat"/></svg>
    <div class="photo" role="img" aria-label="Photo of the coach smiling, hand on hip"></div>
  </article>

  <article class="post">
    <div class="copy"><h2 class="headline" style="--fs:23px">Built for women who are <em class="accent">tired of doing this alone</em></h2><div class="divider"><svg><use href="#i-heart"/></svg></div><p class="tagline">Stay Consistent with<span>RT in Your Pocket!</span></p></div>
    <svg class="icon"><use href="#i-heart"/></svg>
    <div class="photo duo" style="height:68%" role="img" aria-label="Photo of two women standing together laughing"></div>
  </article>

  <article class="post">
    <div class="copy"><h2 class="headline" style="--fs:24px">One Bad Meal <em class="accent">Doesn’t Mean You Failed</em></h2><div class="divider"><svg><use href="#i-heart"/></svg></div><p class="tagline">Stay Consistent with<span>RT in Your Pocket!</span></p></div>
    <svg class="icon"><use href="#i-heart"/></svg>
    <div class="photo hug" role="img" aria-label="Photo of two women sharing a joyful hug"></div>
  </article>

</main>
</body>
</html>
```